Spanish Student Needs a Cover for his PhD Dissertation

Hi everyone :) So, I'm a Corneal surgeon currently finishing my PhD, with a dissertation focused on the evaluation of quality of life in patients affected by a disease called Keratoconus. Just so you know, Keratoconus is a condition in which the cornea (the frontal part of the way) gets thin and bulgy and it decreases vision. What I did during my PhD was designing a questionnaire for evaluating quality of life in this kind of patients.
I need to design a hard cover for my dissertation, which is 200 sheets long. I like kind of minimalistic and geometric designs but I am totally open to suggestions. What needs to be in the cover is the name of the dissertation "Diseño, desarrollo y validación de una encuesta para evaluar el compromiso visual y emocional subjetivos en pacientes con Queratocono" and my name, "Iker Zurmendi". The other thing that needs to go there is the logo of my university (Universidad de Montehierro). Aside from that, anything else is up to the designer. It would be important to use the kind of "red" color I am using in the dissertation. I am attaching the frontal page of my dissertation so you know what kind of design and colors I am using.
In the back part, of the cover, there should be this small inscription: "Iker Zurmendi, MD, es un Oftalmólogo Subespecialista en Cirugía Refractiva de la Universidad Tecnológica Cordillerana (Colombia) y la Universidad de Montehierro (España). Actualmente se desempeña como miembro del Departamento de Córnea y Cirugía Refractiva de la Clínica de Oftalmología Miraluz y como director de su propia compañía de emprendimiento médico Silver Heron Surgical". Please leave a space to place my picture; I will have it taken this week so I don't have it right now, you can just leave the blank spot and I will include it later
The size of the pages is standard "letter" size.
Thanks a lot!

Target Market(s)

PhD Scholars

Font styles to use
Serif

Requirements
Must have
• The "red" color I use on my font. It must be formal but "young".
Nice to have
• I like to keep the design clean, kind of "formal with a young" touch so to speak. I really like gray colors, so it would be nice to have broad areas of gray. I love geometrical designs.
I have uploaded a very early version a friend of mine made (it even had a different title); this can be a starting point for you to work on, but I am more than open to suggestions and new ideas.
Should not have
• Please don't use my whole name, Iker Zurmendi is fine. I don't like ALL CAPITALS.

```html
<!DOCTYPE html>
<html lang="es">
<head>
<meta charset="utf-8">
<title>Queratocono – Tesis doctoral – Iker Zurmendi</title>
<link rel="stylesheet" href="https://fonts.googleapis.com/css2?family=Barlow+Condensed:wght@600&family=Barlow:wght@300;400;600&display=swap">
<style>
  :root{
    --bg:#e4e5e7;
    --ink-dark:#17141f;
    --paper:#ffffff;
    --brand-red:#a3112a;
    --cover-red:#8e1518;
    --photo-light:#c9c9c9;
    --photo-mid:#8a8a8a;
    --photo-dark:#3c3c3c;
    --back-grey:#2f2f30;
    --strip:#d9d9d9;
    --text-light:#f2f2f2;
    --text-muted:#b9b9b9;
    --accent-a:#f0a21a;
    --accent-b:#d0241c;
  }
  *{margin:0;padding:0;box-sizing:border-box}
  html,body{width:1200px;height:1142px;overflow:hidden}
  body{background:var(--bg);position:relative;font-family:"Barlow",sans-serif}

  .cover{position:absolute;top:234px;width:520px;height:673px;overflow:hidden;box-shadow:0 10px 30px rgba(0,0,0,.18)}
  .cover--front{left:50px}
  .cover--back{left:630px;background:var(--back-grey)}

  .cover__art{position:absolute;inset:0;width:100%;height:100%}

  .brand{position:absolute;left:300px;width:200px;text-align:center}
  .brand--university{top:62px}
  .brand__seal{width:48px;height:48px;border-radius:50%;border:2px solid var(--brand-red);margin:0 auto 8px}
  .brand__name{font-family:"Barlow Condensed",sans-serif;font-weight:600;color:var(--brand-red);font-size:14px;letter-spacing:.2px}
  .brand--school{top:152px}
  .brand--school .brand__name{color:var(--ink-dark);font-size:12px}

  .title-block{position:absolute;left:290px;top:348px;width:220px}
  .rule{height:2px;width:140px;background:linear-gradient(90deg,var(--accent-a),var(--accent-b))}
  .title{font-family:"Barlow Condensed",sans-serif;font-weight:600;color:var(--text-light);font-size:27px;line-height:28px;margin:10px 0 8px}
  .author{font-family:"Barlow",sans-serif;font-weight:300;color:var(--text-muted);font-size:19px;letter-spacing:.8px;margin-top:4px}

  .strip{position:absolute;left:0;top:0;width:106px;height:100%;background:linear-gradient(90deg,#cfcfcf,var(--strip) 40%,#f0f0f0)}
  .portrait-slot{position:absolute;left:128px;top:176px;width:74px;height:90px;background:#9c9c9c;border:1px solid #bdbdbd}
  .bio{position:absolute;left:128px;top:280px;width:228px;color:var(--text-light);font-size:12.5px;line-height:17px;letter-spacing:.3px}
  .bio__name{display:block;font-weight:600;font-size:14.5px;margin-bottom:3px}
</style>
</head>
<body>

<section class="cover cover--front" aria-label="Portada">
  <svg class="cover__art" viewBox="0 0 520 673" preserveAspectRatio="none">
    <defs>
      <linearGradient id="eyeTone" x1="0" y1="0" x2="1" y2="1">
        <stop offset="0" stop-color="var(--photo-light)"/>
        <stop offset=".45" stop-color="var(--photo-mid)"/>
        <stop offset="1" stop-color="var(--photo-dark)"/>
      </linearGradient>
    </defs>
    <g role="img" aria-label="Fotografía en blanco y negro de un ojo visto de perfil, con la córnea abombada">
      <rect x="0" y="0" width="520" height="673" fill="url(#eyeTone)"/>
    </g>
    <polygon points="0,0 162,0 310,148 0,218" fill="var(--ink-dark)"/>
    <polygon points="162,0 520,0 520,378" fill="var(--paper)"/>
    <polygon points="0,400 0,673 200,673" fill="var(--cover-red)"/>
  </svg>

  <div class="brand brand--university">
    <div class="brand__seal"></div>
    <div class="brand__name">Universidad de Montehierro</div>
  </div>
  <div class="brand brand--school">
    <div class="brand__name">Escuela de Doctorado Montehierro</div>
  </div>

  <div class="title-block">
    <div class="rule"></div>
    <h1 class="title">Diseño, desarrollo y validación de una encuesta para evaluar el compromiso visual y emocional subjetivos en pacientes con Queratocono</h1>
    <div class="rule"></div>
    <p class="author">Iker Zurmendi</p>
  </div>
</section>

<section class="cover cover--back" aria-label="Contraportada">
  <div class="strip"></div>
  <div class="portrait-slot" role="img" aria-label="Espacio reservado para la fotografía del autor"></div>
  <p class="bio">
    <span class="bio__name">Iker Zurmendi, MD,</span>
    es un Oftalmólogo Subespecialista en Cirugía Refractiva de la Universidad Tecnológica Cordillerana (Colombia) y la Universidad de Montehierro (España). Actualmente se desempeña como miembro del Departamento de Córnea y Cirugía Refractiva de la Clínica de Oftalmología Miraluz y como director de su propia compañía de emprendimiento médico Silver Heron Surgical
  </p>
</section>

</body>
</html>
```